The most modern business card ever !!!

Our company call “Vendalo”. Vendalo is a technology company specialized in cruises solutions. Out main product is a platform to reserve cruises. This is a revolutionary platform that make easier to travel agencies and final users to reserve cruises across dozen companies like tibba, wernu, hpv, dgb, etc..We are a “start up”, with a young team of developers and we want to transmit it.. For it, we want something different, a modern business card that represent cruises and technology.. When someone receive this card, this person should say: wowww this is different… this is modern… this is a cruise related company..
- diferent, modern
- traditions business card

```html
<!DOCTYPE html>
<html lang="en">
<head>
<meta charset="utf-8">
<title>Vendalo Business Card</title>
<link rel="stylesheet" href="https://fonts.googleapis.com/css2?family=Exo+2:wght@500;600&family=Roboto:wght@400;700&display=swap">
<style>
  :root {
    --bg: #e7e4df;
    --card-black: #060606;
    --brand-blue: #23a7e0;
    --paper-white: #ffffff;
    --ink-dark: #0d0d0d;
    --text-light: #f4f4f4;
  }
  html, body {
    margin: 0;
    padding: 0;
    overflow: hidden;
  }
  body {
    width: 1200px;
    height: 880px;
    background: var(--bg);
    position: relative;
  }
  .card {
    position: absolute;
    width: 640px;
    height: 366px;
    border-radius: 22px;
    overflow: hidden;
    background: var(--card-black);
    box-shadow: 0 14px 30px rgba(0,0,0,0.25);
  }
  .card svg { display: block; }
  .card-front { left: 70px; top: 50px; }
  .card-back { left: 490px; top: 464px; }

  .wordmark {
    font-family: "Exo 2", sans-serif;
    font-weight: 600;
    letter-spacing: 1px;
  }
  .wordmark-front { fill: var(--text-light); font-size: 84px; }
  .wordmark-back { fill: var(--ink-dark); font-size: 62px; }

  .person-name {
    font-family: "Exo 2", sans-serif;
    font-weight: 500;
    font-size: 27px;
    fill: var(--text-light);
  }
  .person-title {
    font-family: "Roboto", sans-serif;
    font-size: 16px;
    fill: var(--brand-blue);
  }
  .contact-line {
    font-family: "Roboto", sans-serif;
    font-size: 17px;
    fill: var(--text-light);
  }
  .website {
    font-family: "Roboto", sans-serif;
    font-weight: 700;
    font-size: 18px;
    letter-spacing: 0.5px;
    fill: var(--text-light);
  }
  .website-accent { fill: var(--brand-blue); }
</style>
</head>
<body>

  <!-- Front side -->
  <div class="card card-front">
    <svg width="640" height="366" viewBox="0 0 640 366">
      <rect class="card-base" width="640" height="366" fill="var(--card-black)"/>
      <polygon class="stripe-thin" points="58,120 104,120 36,366 0,366 0,300" fill="var(--brand-blue)"/>
      <path class="chevron" d="M240,0 H330 L214,232 Q200,262 234,262 H470 L498,318 H160 Q100,318 122,268 Z" fill="var(--brand-blue)"/>
      <polygon class="stripe-base" points="60,366 520,366 545,344 70,344" fill="var(--brand-blue)"/>
      <text class="wordmark wordmark-front" x="590" y="258" text-anchor="end">Vendalo</text>
    </svg>
  </div>

  <!-- Back side -->
  <div class="card card-back">
    <svg width="640" height="366" viewBox="0 0 640 366">
      <rect class="card-base" width="640" height="366" fill="var(--card-black)"/>
      <path class="panel-outline" d="M0,112 H342 Q394,112 392,164 L386,366" fill="none" stroke="var(--brand-blue)" stroke-width="9"/>
      <path class="panel-white" d="M0,128 H328 Q376,128 374,176 L368,366 H0 Z" fill="var(--paper-white)"/>
      <text class="wordmark wordmark-back" x="186" y="268" text-anchor="middle">Vendalo</text>

      <text class="person-name" x="515" y="62" text-anchor="middle">Lena Marsh</text>
      <text class="person-title" x="515" y="84" text-anchor="middle">President</text>

      <g class="icon-phone" transform="translate(515,122)">
        <circle r="15" fill="var(--brand-blue)"/>
        <circle r="11" fill="var(--paper-white)"/>
        <path d="M-6,-4 Q-6,-7 -3,-7 L3,-7 Q6,-7 6,-4 L4,-2 L2,-3 L-2,-3 L-4,-2 Z M-5,0 H5 V5 H-5 Z" fill="var(--ink-dark)"/>
      </g>
      <text class="contact-line" x="515" y="162" text-anchor="middle">+(0) 21 480 7316</text>
      <line class="divider" x1="420" y1="178" x2="610" y2="178" stroke="var(--brand-blue)" stroke-width="1"/>

      <g class="icon-mail" transform="translate(515,212)">
        <circle r="15" fill="var(--brand-blue)"/>
        <circle r="11" fill="var(--paper-white)"/>
        <rect x="-6" y="-4" width="12" height="8" fill="var(--ink-dark)"/>
        <polyline points="-6,-4 0,1 6,-4" fill="none" stroke="var(--paper-white)" stroke-width="1.2"/>
      </g>
      <text class="contact-line" x="515" y="252" text-anchor="middle">info@vendalo.io</text>

      <text class="website" x="512" y="302" text-anchor="middle">www.<tspan class="website-accent">VENDALO</tspan>.com</text>
    </svg>
  </div>

</body>
</html>
```